Business card - KT Placement Partners / The Danford Group

We need a business card and logo design for my executive search (recruiting / headhunting) firm. We find people to fill open jobs at companies. We are a U.S. based company and do some global work also. So maybe something with a globe but definitely looking for other options also. Maybe something incorporating the letters KT which is our current logo but looking at options. The card should say BOTH full company names and tag line-

KT Placement Partners / The Danford Group
Executive Search Results You Can Count On

The design should say about the company-
Sharp
Reliable
Find the best people for the job
Business oriented
Results achieved
Modern

Target Market(s)

Business owners, CEO's, and heads of human resources departments

Industry/Entity Type

Business Consultant

Contact Information for Business Card

The card MUST say BOTH full company names and tag line-

Logo Text

Logo does not NEED to say anything on the design itself, but could if designed that way.

Font styles to use
Serif
Sans Serif

Requirements
Must have
• The business cards need to have. In addition to name, title, address, phone, website, and email address,
• The card MUST say BOTH full company names and tag line-
• KT Placement Partners / The Danford Group
• Executive Search Results You Can Count On
Nice to have
• The design should say about the company-
• Sharp
• Reliable
• Find the best people for the job
• Business oriented
• Results achieved
• Modern
• Maybe something with a globe or the letters KT or relating to people. Open to options.
Should not have
• Should not be cutesy or funny, for this design

```html
<!DOCTYPE html>
<html lang="en">
<head>
<meta charset="utf-8">
<title>KT Placement Partners – Business Card</title>
<link href="https://fonts.googleapis.com/css2?family=Lato:wght@400;700;900&family=Montserrat:wght@600;700&display=swap" rel="stylesheet">
<style>
  :root{
    --stage:#1c1c1e;
    --navy:#0f3a6e;
    --navy-deep:#0b2f5c;
    --ink:#2b2b2b;
    --paper:#fbfbfb;
    --rule:#3a3a3a;
    --map-a:#e6e7f2;
    --map-b:#d5d7e8;
    --white:#ffffff;
  }
  *{margin:0;padding:0;box-sizing:border-box}
  html,body{width:1200px;height:873px;overflow:hidden;background:var(--stage)}
  .stage{position:relative;width:1200px;height:873px}
  .card{position:absolute;width:540px;height:309px;border-radius:3px;overflow:hidden;box-shadow:0 10px 30px rgba(0,0,0,.45)}

  /* Front */
  .card--front{left:40px;top:282px;background:linear-gradient(135deg,var(--navy) 0%,var(--navy-deep) 100%)}
  .lockup{position:absolute;display:flex;align-items:center;gap:12px}
  .lockup__mark{width:14px;height:14px;border-radius:50%;flex:none}
  .lockup__name,.lockup__group{font-family:'Lato',sans-serif;font-weight:400;line-height:1.1;white-space:nowrap}
  .lockup__group{letter-spacing:.28em;text-transform:uppercase}
  .card--front .lockup{left:70px;top:112px}
  .card--front .lockup__mark{background:var(--white)}
  .card--front .lockup__name,.card--front .lockup__group{color:var(--white)}
  .card--front .lockup__name{font-size:30px}
  .card--front .lockup__group{font-size:20px;margin-top:4px}

  /* Back */
  .card--back{left:620px;top:282px;background:var(--paper)}
  .card--back .lockup{left:40px;top:26px}
  .card--back .lockup__mark{background:var(--navy)}
  .card--back .lockup__name,.card--back .lockup__group{color:var(--navy)}
  .card--back .lockup__name{font-size:19px}
  .card--back .lockup__group{font-size:13px;margin-top:3px}

  .world-map{position:absolute;left:70px;top:55px;width:440px;height:150px;border-radius:40px;background:radial-gradient(ellipse at center,var(--map-b) 0%,var(--map-a) 60%,rgba(230,231,242,0) 100%)}

  .person{position:absolute;right:24px;top:92px;text-align:right;width:190px;border-bottom:1.5px solid var(--rule);padding-bottom:2px}
  .person__name{font-family:'Lato',sans-serif;font-size:17px;color:var(--navy);font-weight:400}
  .person__name b{font-weight:900}
  .person__title{font-family:'Lato',sans-serif;font-size:10px;color:var(--ink);font-weight:700}

  .contact{position:absolute;left:22px;top:172px;width:270px}
  .contact__address{font-family:'Lato',sans-serif;font-weight:900;font-size:12px;color:var(--navy);border-top:1.5px solid var(--rule);padding-top:8px}
  .contact__list{list-style:none;margin-top:5px}
  .contact__item{display:flex;align-items:center;gap:9px;font-family:'Lato',sans-serif;font-size:12px;color:var(--ink);height:18px;white-space:nowrap}
  .contact__icon{width:13px;height:13px;fill:var(--navy);flex:none}

  .tagline{position:absolute;right:24px;bottom:16px;font-family:'Montserrat',sans-serif;font-weight:700;font-size:13px;letter-spacing:.12em;color:var(--navy);white-space:nowrap}
</style>
</head>
<body>
<main class="stage">
  <section class="card card--front" aria-label="Business card front">
    <div class="lockup">
      <span class="lockup__mark"></span>
      <div>
        <div class="lockup__name">KT Placement Partners</div>
        <div class="lockup__group">The Danford Group</div>
      </div>
    </div>
  </section>

  <section class="card card--back" aria-label="Business card back">
    <div class="world-map" role="img" aria-label="Dotted world map in soft lavender grey"></div>

    <div class="lockup">
      <span class="lockup__mark"></span>
      <div>
        <div class="lockup__name">KT Placement Partners</div>
        <div class="lockup__group">The Danford Group</div>
      </div>
    </div>

    <div class="person">
      <div class="person__name">Marcus <b>Hale</b></div>
      <div class="person__title">Athletic Director</div>
    </div>

    <div class="contact">
      <div class="contact__address">248 Alder Lane, Greenfield, PA 15207</div>
      <ul class="contact__list">
        <li class="contact__item">
          <svg class="contact__icon" viewBox="0 0 16 16"><path d="M1 6c0-2 3-3 7-3s7 1 7 3v1h-4V5.5H5V7H1zM4 8h8l2 6H2z"/></svg>
          412-555-0147
        </li>
        <li class="contact__item">
          <svg class="contact__icon" viewBox="0 0 16 16"><rect x="4" y="1" width="8" height="4"/><rect x="1" y="6" width="14" height="6" rx="1"/><rect x="4" y="10" width="8" height="5" fill="#fff" stroke="#0f3a6e" stroke-width="1.2"/></svg>
          412-555-0193
        </li>
        <li class="contact__item">
          <svg class="contact__icon" viewBox="0 0 16 16"><rect x="1" y="3" width="14" height="10"/><path d="M1.5 3.5 8 9l6.5-5.5" fill="none" stroke="#fff" stroke-width="1.3"/></svg>
          mhale@ktplacementpartners
        </li>
      </ul>
    </div>

    <div class="tagline">Executive Search Results You Can Count On</div>
  </section>
</main>
</body>
</html>
```